Flyer for the Radiant Harvest Worship Day

I am looking to create a flyer for a one day prayer retreat our church is organizing.
This flyer will be posted on social media, websites and will also be printed so it can be mailed to people.
I am looking for something professional, with good use of our logo and band colors (logo colors).
I am counting on the designer's skill, creativity, art and knowledge of media communication to produce a flyer that will effectively and quickly convey the message we are trying to spread.
CONTENT OF THE FLYER:
Event title: Radiant Harvest Worship Day
Date: Tuesday July 2nd, 2019
Time: 11:00AM - 7:00PM
Belmora Hotel, 4875 Wexley Avenue, Portland, Maine 04102 (Room: Juniper)
Event Key words to highlight what the event is about: Prayer, Sharing the Word, Panel discussion, prophecy, Impartation.
Key phrases:
A one day prayer retreat.
Jesus Chris is Lord
Contact info:
www.tolvex.org
Phone: 207 555 3184
Email: contact@brookhavenfold.org

```html
<!DOCTYPE html>
<html lang="en">
<head>
<meta charset="utf-8">
<title>Radiant Harvest Worship Day</title>
<link rel="stylesheet" href="https://fonts.googleapis.com/css2?family=Bebas+Neue&family=Arimo:wght@400;700&display=swap">
<style>
  :root {
    --navy: #0e3558;
    --orange: #f29422;
    --white: #ffffff;
    --rule: #c9a46a;
    --sky-top: #7a5a48;
    --sky-mid: #f0b060;
    --sky-glow: #fde2a8;
    --field: #3a2c22;
  }
  * { margin: 0; padding: 0; box-sizing: border-box; }
  html, body { width: 866px; height: 1200px; overflow: hidden; background: var(--white); }
  .flyer {
    position: relative; width: 866px; height: 1200px;
    background: var(--white); border: 1px solid #8a8a8a;
    font-family: "Arimo", Arial, sans-serif;
  }
  .panel {
    position: absolute; left: 42px; top: 47px; width: 781px; height: 1104px;
    background: var(--navy);
  }
  .hero {
    position: absolute; left: 0; top: 34px; width: 781px; height: 538px;
    border-top: 2px solid var(--white); border-bottom: 2px solid var(--white);
    background:
      radial-gradient(ellipse 260px 200px at 48% 46%, var(--sky-glow), rgba(253,226,168,0) 100%),
      linear-gradient(180deg, var(--sky-top) 0%, #c98350 22%, var(--sky-mid) 45%, #d9924a 62%, #7a5030 74%, var(--field) 90%, #1c1b22 100%);
  }
  .event-title {
    position: absolute; left: 54px; top: 80px;
    font-family: "Bebas Neue", Impact, sans-serif; font-weight: 400; line-height: 0.98;
  }
  .event-title .line-one { display: block; color: var(--white); font-size: 60px; }
  .event-title .line-two { display: block; color: var(--navy); font-size: 82px; }
  .logo-box {
    position: absolute; right: 41px; top: 36px; width: 233px; height: 198px;
    background: var(--navy);
    display: flex; align-items: center; justify-content: center; gap: 10px;
  }
  .brand-name {
    color: var(--white); font-family: "Arimo", Arial, sans-serif; font-weight: 400;
    font-size: 40px; letter-spacing: 1px; white-space: nowrap;
  }
  .brand-dot { width: 16px; height: 16px; border-radius: 50%; background: var(--orange); flex: none; }
  .headline {
    position: absolute; left: 0; width: 100%; top: 478px; text-align: center;
    font-family: "Bebas Neue", Impact, sans-serif; font-weight: 400; font-size: 84px; color: var(--white);
    line-height: 1;
  }
  .tagline-band {
    position: absolute; left: 0; top: 580px; width: 781px; height: 41px;
    background: var(--orange); color: var(--navy);
    font-weight: 700; font-size: 25px; text-align: center; line-height: 41px;
  }
  .keywords {
    position: absolute; left: 0; top: 668px; width: 100%; text-align: center;
    color: var(--white); font-weight: 700; font-size: 32px; line-height: 39px;
  }
  .details { position: absolute; top: 810px; left: 0; width: 100%; color: var(--white); font-size: 25px; line-height: 36.5px; }
  .detail { position: absolute; top: 0; }
  .detail .icon { position: absolute; left: 0; top: 0; width: 37px; height: 37px; }
  .detail-date { left: 62px; width: 190px; }
  .detail-date .first { padding-left: 49px; }
  .detail-date .second { padding-left: 12px; }
  .detail-time { left: 271px; width: 154px; text-align: right; }
  .detail-place { left: 455px; width: 310px; }
  .detail-place .first { padding-left: 55px; }
  .detail-place .lead { padding-left: 3px; }
  .detail-place .room { padding-left: 11px; }
  .divider { position: absolute; top: -2px; width: 1px; height: 106px; background: var(--rule); }
  .footer-rule { position: absolute; left: 36px; top: 988px; width: 712px; height: 1px; background: #9fb0c2; }
  .footer-brand {
    position: absolute; left: 74px; top: 992px; height: 50px; display: flex; align-items: center; gap: 10px;
  }
  .footer-brand .brand-name { font-size: 38px; }
  .contacts { position: absolute; left: 276px; top: 1002px; color: var(--white); font-size: 29px; line-height: 38px; }
  .contacts .row { display: flex; align-items: center; gap: 8px; }
  .contacts svg { width: 24px; height: 24px; flex: none; }
</style>
</head>
<body>
<div class="flyer">
  <div class="panel">
    <div class="hero" role="img" aria-label="Photo of a person with outstretched arms standing in a grassy field under a glowing sunset sky"></div>

    <h1 class="event-title">
      <span class="line-one">RADIANT HARVEST</span>
      <span class="line-two">WORSHIP DAY</span>
    </h1>

    <div class="logo-box">
      <span class="brand-dot"></span>
      <span class="brand-name">TOLVEX</span>
    </div>

    <p class="headline">A ONE DAY PRAYER RETREAT.</p>

    <p class="tagline-band">JESUS CHRIS IS LORD</p>

    <p class="keywords">Prayer | Sharing the Word<br>Panel discussion | Prophecy | Impartation.</p>

    <div class="details">
      <div class="detail detail-date">
        <svg class="icon" viewBox="0 0 32 32"><circle cx="16" cy="16" r="16" fill="#f29422"/><rect x="9" y="10" width="14" height="13" rx="1.5" fill="none" stroke="#fff" stroke-width="1.6"/><line x1="9" y1="14" x2="23" y2="14" stroke="#fff" stroke-width="1.6"/><line x1="12.5" y1="8" x2="12.5" y2="11.5" stroke="#fff" stroke-width="1.6"/><line x1="19.5" y1="8" x2="19.5" y2="11.5" stroke="#fff" stroke-width="1.6"/></svg>
        <div class="first">Tuesday</div>
        <div class="second">July 2nd, 2019</div>
      </div>
      <div class="divider" style="left:255px"></div>
      <div class="detail detail-time">
        <svg class="icon" viewBox="0 0 32 32"><circle cx="16" cy="16" r="16" fill="#f29422"/><circle cx="16" cy="16" r="8" fill="none" stroke="#fff" stroke-width="1.6"/><polyline points="16,11 16,16 19.5,18" fill="none" stroke="#fff" stroke-width="1.6"/></svg>
        <div>11:00AM</div>
        <div>to 7:00PM</div>
      </div>
      <div class="divider" style="left:441px"></div>
      <div class="detail detail-place">
        <svg class="icon" viewBox="0 0 32 32"><circle cx="16" cy="16" r="16" fill="#f29422"/><path d="M16 25c-4-5-6.5-8.2-6.5-11.3a6.5 6.5 0 0 1 13 0C22.5 16.8 20 20 16 25z" fill="none" stroke="#fff" stroke-width="1.6"/><circle cx="16" cy="13.6" r="2.4" fill="none" stroke="#fff" stroke-width="1.6"/></svg>
        <div class="first">Belmora Hotel,</div>
        <div class="lead">4875 Wexley Avenue,</div>
        <div class="lead">Portland, Maine 04102</div>
        <div class="room">(Room: Juniper)</div>
      </div>
    </div>

    <div class="footer-rule"></div>

    <div class="footer-brand">
      <span class="brand-dot"></span>
      <span class="brand-name">TOLVEX</span>
    </div>

    <div class="contacts">
      <div class="row">
        <svg viewBox="0 0 24 24"><circle cx="12" cy="12" r="9.5" fill="none" stroke="#fff" stroke-width="1.4"/><ellipse cx="12" cy="12" rx="4.2" ry="9.5" fill="none" stroke="#fff" stroke-width="1.4"/><line x1="2.5" y1="12" x2="21.5" y2="12" stroke="#fff" stroke-width="1.4"/></svg>
        <span>tolvex.org</span>
        <svg viewBox="0 0 24 24" style="margin-left:10px"><path d="M3 10c0-3 4-5 9-5s9 2 9 5l-3 1-1.5-2.5h-9L6 11z" fill="none" stroke="#fff" stroke-width="1.4"/><rect x="6" y="12" width="12" height="7" rx="1.5" fill="none" stroke="#fff" stroke-width="1.4"/></svg>
        <span>207 555 3184</span>
      </div>
      <div class="row">
        <svg viewBox="0 0 24 24"><rect x="3" y="6" width="18" height="12" fill="none" stroke="#fff" stroke-width="1.4"/><polyline points="3,6 12,13 21,6" fill="none" stroke="#fff" stroke-width="1.4"/></svg>
        <span>contact@brookhavenfold.org</span>
      </div>
    </div>
  </div>
</div>
</body>
</html>
```